Advertising company unique advertising platform

we need a logo design for a new company based in Australia Melbourne. We develop innovated advertising platform where consumer can use this platform to get regular discount, as business owner they can use this platform for free advertisement. Payment for this advertisement platform only payable every two weeks, when I generate revenue for their business

Industry/Entity Type

Advertising

Contact Information for Business Card

Dale Morven | Co-Founder |Managing Director
Suite 718 240 Wattlebrook Lane Melbourne Vic 3000

ABN 38 614 207 923
Tel: +61 0487 259 318 | Email: dale.morven@plivorantu.com

Font styles to use
Decorative
Script

Requirements
Must have
• Try few different design and some round corner business card
Should not have
• One round corner business card...try 4 different colour background not only black, make sure two side is designed. Be creative so imagine you are giving this to a client make sure has wow factor, if you can also try one design with engrave like all the logo, words look 3d feel
• The word Advertising Platform use attached file font

```html
<!DOCTYPE html>
<html lang="en">
<head>
<meta charset="utf-8">
<title>Adverlume Business Card</title>
<link rel="stylesheet" href="https://fonts.googleapis.com/css2?family=Cinzel:wght@400&family=Work+Sans:wght@400;500;600&display=swap">
<style>
  :root {
    --page: #ece8e2;
    --card-dark: #2a2a2a;
    --card-dark-edge: #353535;
    --card-light: #ffffff;
    --brand-orange: #f08a2c;
    --ink: #1f1f1f;
    --muted: #3a3a3a;
    --band: #262626;
  }
  * { box-sizing: border-box; margin: 0; padding: 0; }
  html, body { width: 1200px; height: 900px; overflow: hidden; }
  body {
    background: var(--page);
    font-family: "Work Sans", Arial, sans-serif;
    position: relative;
  }
  .card {
    position: absolute;
    left: 250px;
    width: 700px;
    height: 400px;
    box-shadow: 0 10px 28px rgba(0,0,0,0.18);
    overflow: hidden;
  }
  .card-front {
    top: 40px;
    background: radial-gradient(ellipse at 55% 40%, var(--card-dark-edge), var(--card-dark) 70%);
    display: flex;
    align-items: center;
    justify-content: center;
  }
  .card-back { top: 460px; background: var(--card-light); }

  .brand {
    display: flex;
    align-items: center;
    gap: 16px;
  }
  .brand-dot {
    border-radius: 50%;
    background: var(--brand-orange);
    flex: none;
  }
  .brand-name {
    font-family: "Work Sans", Arial, sans-serif;
    font-weight: 600;
    color: var(--brand-orange);
    letter-spacing: 0.02em;
  }
  .card-front .brand-dot { width: 86px; height: 86px; }
  .card-front .brand-name { font-size: 58px; }

  .card-back .brand {
    position: absolute;
    top: 46px;
    right: 46px;
    gap: 12px;
  }
  .card-back .brand-dot { width: 58px; height: 58px; }
  .card-back .brand-name { font-size: 38px; }

  .contact {
    position: absolute;
    left: 52px;
    bottom: 40px;
    color: var(--ink);
  }
  .person-name {
    font-family: "Cinzel", Georgia, serif;
    font-size: 34px;
    color: var(--brand-orange);
    letter-spacing: 0.02em;
    line-height: 1;
  }
  .person-role {
    font-family: "Cinzel", Georgia, serif;
    font-size: 13px;
    color: var(--muted);
    margin: 6px 0 10px;
    letter-spacing: 0.03em;
  }
  .address { font-size: 17px; line-height: 1.3; margin-bottom: 8px; }
  .contact-line {
    display: flex;
    align-items: center;
    gap: 10px;
    font-size: 17px;
    line-height: 1.35;
  }
  .contact-line svg { width: 13px; height: 13px; flex: none; }

  .abn-band {
    position: absolute;
    right: 0;
    bottom: 112px;
    width: 235px;
    height: 34px;
    background: var(--band);
    color: #fff;
    font-size: 15px;
    display: flex;
    align-items: center;
    padding-left: 22px;
    gap: 6px;
  }
  .abn-label { color: var(--brand-orange); }
</style>
</head>
<body>
  <section class="card card-front">
    <div class="brand">
      <span class="brand-dot"></span>
      <span class="brand-name">Adverlume</span>
    </div>
  </section>

  <section class="card card-back">
    <div class="brand">
      <span class="brand-dot"></span>
      <span class="brand-name">Adverlume</span>
    </div>

    <div class="abn-band"><span class="abn-label">ABN:</span> 38 614 207 923</div>

    <div class="contact">
      <h1 class="person-name">DALE MORVEN</h1>
      <p class="person-role">|CO-FOUNDER | MANAGING DIRECTOR</p>
      <p class="address">Suite 718 240 Wattlebrook<br>Lane Melbourne Vic 3000</p>
      <p class="contact-line">
        <svg viewBox="0 0 16 16" aria-hidden="true"><path d="M3 1.5l3 .5 1 3.5-2 1.5a9 9 0 0 0 4.5 4.5l1.5-2 3.5 1 .5 3-2 1.5C7 15 1 9 1.5 3.5z" fill="var(--brand-orange)"/></svg>
        +61 0487 259 318
      </p>
      <p class="contact-line">
        <svg viewBox="0 0 16 16" aria-hidden="true"><rect x="1.5" y="3.5" width="13" height="9" fill="none" stroke="var(--brand-orange)" stroke-width="1.6"/><path d="M1.5 3.5L8 9l6.5-5.5" fill="none" stroke="var(--brand-orange)" stroke-width="1.6"/></svg>
        dale.morven@plivorantu.com
      </p>
    </div>
  </section>
</body>
</html>
```